Business Card Design for company

We want new business cards. We'd like something different-- yet still highly professional. Our tagline is Providing leadership, delivering success. Stock photos are ok, as long as they are relevant and look upscale.

Target Market(s)

Architecture/Business Management Consulting/Engineering Consulting

Contact Information for Business Card

dark gray background with pops of blue might be good, but you tell me. You're the designers. Rounded corners might be nice, but again, you tell me.

Font styles to use
Serif
Sans Serif

Colors
3276b5
5c5c5c
9d9d9d
fbfbfb

Requirements
Nice to have
• Something different, but still very professional.

```html
<!DOCTYPE html>
<html lang="en">
<head>
<meta charset="utf-8">
<title>Corvane International – Business Card</title>
<link href="https://fonts.googleapis.com/css2?family=Montserrat:wght@400;500;600&display=swap" rel="stylesheet">
<style>
  :root {
    --stage: #1c1a1a;
    --card-dark: #121212;
    --card-mid: #1e1e1e;
    --photo-dark: #1a1a1a;
    --photo-light: #4a4a4a;
    --blue: #3276b5;
    --grey-dark: #5c5c5c;
    --grey-light: #9d9d9d;
    --white: #fbfbfb;
  }
  * { margin: 0; padding: 0; box-sizing: border-box; }
  html, body {
    width: 1200px; height: 890px; overflow: hidden;
    background: var(--stage);
    font-family: "Montserrat", sans-serif;
  }
  .canvas {
    width: 1200px; height: 890px;
    display: flex; flex-direction: column;
    align-items: center; justify-content: center; gap: 40px;
  }
  .card {
    position: relative;
    width: 640px; height: 366px;
    border-radius: 22px;
    overflow: hidden;
    box-shadow: 0 12px 30px rgba(0,0,0,.55);
  }

  /* Front */
  .card-front .city-photo {
    position: absolute; inset: 0;
    background: linear-gradient(160deg, var(--photo-light) 0%, #2e2e2e 45%, var(--photo-dark) 100%);
  }
  .card-front .shade {
    position: absolute; inset: 0;
    background: rgba(0,0,0,.35);
  }
  .front-brand {
    position: absolute; inset: 0;
    display: flex; flex-direction: column;
    align-items: center; justify-content: center;
    text-align: center;
  }
  .brand-name {
    color: var(--white);
    font-weight: 500;
    font-size: 28px;
    letter-spacing: .14em;
    text-transform: uppercase;
    white-space: nowrap;
  }
  .tagline {
    margin-top: 18px;
    color: var(--grey-light);
    font-size: 12px;
    letter-spacing: .16em;
    text-transform: uppercase;
    white-space: nowrap;
  }

  /* Back */
  .card-back {
    background: linear-gradient(135deg, var(--card-mid) 0%, var(--card-dark) 60%, #0b0b0b 100%);
  }
  .back-brand {
    position: absolute; top: 78px; left: 0; right: 0;
    text-align: center;
  }
  .holder {
    position: absolute; left: 56px; top: 180px;
    width: 230px; text-align: right;
  }
  .holder-name {
    color: var(--blue);
    font-weight: 600;
    font-size: 20px;
    letter-spacing: .06em;
    text-transform: uppercase;
    white-space: nowrap;
  }
  .holder-title {
    margin-top: 6px;
    color: var(--grey-light);
    font-size: 14px;
  }
  .divider {
    position: absolute; left: 310px; top: 172px;
    width: 1px; height: 96px;
    background: var(--blue);
  }
  .contact-list {
    position: absolute; left: 334px; top: 176px;
    list-style: none;
  }
  .contact-list li {
    display: flex; align-items: center; gap: 10px;
    color: var(--white);
    font-size: 13px;
    line-height: 22px;
    letter-spacing: .03em;
    white-space: nowrap;
  }
  .contact-list svg { width: 11px; height: 11px; fill: var(--blue); flex: none; }
  .address {
    position: absolute; left: 0; right: 0; bottom: 48px;
    text-align: center;
    color: var(--grey-light);
    font-size: 13px;
    letter-spacing: .04em;
    white-space: nowrap;
  }
</style>
</head>
<body>
<main class="canvas">

  <section class="card card-front">
    <div class="city-photo" role="img" aria-label="Black and white aerial photograph of a city skyline"></div>
    <div class="shade"></div>
    <div class="front-brand">
      <div class="brand-name">Corvane International</div>
      <div class="tagline">Shaping Strategy | Building Results</div>
    </div>
  </section>

  <section class="card card-back">
    <div class="back-brand">
      <div class="brand-name">Corvane International</div>
    </div>
    <div class="holder">
      <div class="holder-name">Daniel Hale</div>
      <div class="holder-title">Design Consultant</div>
    </div>
    <div class="divider"></div>
    <ul class="contact-list">
      <li>
        <svg viewBox="0 0 12 12"><path d="M3 0.5 L5 3 L3.8 4.5 Q5 7 7.5 8.2 L9 7 L11.5 9 L10 11.5 Q5 11 1 5 Q0.5 2 3 0.5Z"/></svg>
        +1 555-010-4827
      </li>
      <li>
        <svg viewBox="0 0 12 12"><path d="M0.5 2h11v8h-11z M1.5 3l4.5 3.5 4.5-3.5v-0.2h-9z" fill-rule="evenodd"/></svg>
        MARKETING@CORVANEINTL.COM
      </li>
      <li>
        <svg viewBox="0 0 12 12"><path d="M0.5 2h11v8h-11z M1.5 3l4.5 3.5 4.5-3.5v-0.2h-9z" fill-rule="evenodd"/></svg>
        INFO@CORVANEINTL.COM
      </li>
      <li>
        <svg viewBox="0 0 12 12"><circle cx="6" cy="6" r="5.5"/></svg>
        www.corvaneintl.com
      </li>
    </ul>
    <div class="address">1480 Harbor Crest Lane Tampa, FL 33602</div>
  </section>

</main>
</body>
</html>
```